Specialised investor in e-mobility and energy wants business card design

We need a business card design that fits our existing corporate design. <The look and feel must be 'sharp'/'clean', dynamic, communicate momentum, professionalism etc (as one would imagine from a firm in the financial sector). We like the idea of a reverse-side of the card that includes the logo, and the name and contact details on the other. We expect the deliverable to be whatever format might be required to be able to get cards printed directly by a service such as kelmo press. Our website is www.zub.capital

```html
<!DOCTYPE html>
<html lang="en">
<head>
<meta charset="utf-8">
<title>Zub Capital – Business Card</title>
<link href="https://fonts.googleapis.com/css2?family=Montserrat:wght@400;500;700&display=swap" rel="stylesheet">
<style>
  :root {
    --bg: #d9d9d6;
    --card: #ffffff;
    --green-dark: #2e4d20;
    --green-light: #7db343;
    --ink: #2b2b2b;
  }
  * { margin: 0; padding: 0; box-sizing: border-box; }
  html, body { width: 1200px; height: 801px; overflow: hidden; }
  body {
    background: var(--bg);
    font-family: "Montserrat", sans-serif;
    position: relative;
  }
  .card {
    position: absolute;
    top: 245px;
    width: 540px;
    height: 310px;
    background: var(--card);
    border-bottom: 3px solid var(--green-light);
    box-shadow: 0 10px 24px rgba(0,0,0,0.18);
  }
  .card--front { left: 40px; }
  .card--back { left: 620px; }

  .wordmark {
    color: var(--green-dark);
    font-weight: 500;
    letter-spacing: 0.5px;
    display: flex;
    align-items: center;
    white-space: nowrap;
  }
  .wordmark__dot {
    width: 0.42em;
    height: 0.42em;
    border-radius: 50%;
    background: var(--green-dark);
    margin-right: 0.3em;
  }
  .card--front .wordmark {
    position: absolute;
    left: 34px;
    top: 40px;
    font-size: 40px;
  }
  .card--back .wordmark {
    position: absolute;
    left: 0; right: 0; top: 0; bottom: 0;
    justify-content: center;
    font-size: 60px;
  }

  .divider {
    position: absolute;
    left: 34px;
    top: 176px;
    width: 300px;
    height: 1.5px;
    background: var(--green-light);
  }
  .person {
    position: absolute;
    right: 30px;
    top: 150px;
    text-align: left;
  }
  .person__name {
    color: var(--green-light);
    font-weight: 700;
    font-size: 17px;
    letter-spacing: 0.3px;
    line-height: 1.1;
  }
  .person__role {
    color: var(--ink);
    font-size: 12px;
    margin-top: 2px;
    padding-left: 14px;
  }
  .company {
    position: absolute;
    right: 30px;
    top: 212px;
    text-align: right;
    font-size: 12px;
    line-height: 1.35;
  }
  .company__name { color: var(--green-light); }
  .company__city { color: var(--ink); }

  .contacts {
    position: absolute;
    left: 44px;
    top: 200px;
    list-style: none;
    font-size: 12.5px;
    color: var(--ink);
    line-height: 1.55;
  }
  .contacts li { display: flex; align-items: center; gap: 8px; }
  .contacts svg { width: 11px; height: 11px; fill: var(--green-light); flex: none; }
</style>
</head>
<body>

  <section class="card card--front" aria-label="Business card front">
    <div class="wordmark"><span class="wordmark__dot"></span>zub capital</div>

    <div class="divider"></div>

    <div class="person">
      <p class="person__name">MARK ELLERY</p>
      <p class="person__role">Managing Director</p>
    </div>

    <div class="company">
      <p class="company__name">Zub Capital S.A.</p>
      <p class="company__city">Geneva, Switzerland</p>
    </div>

    <ul class="contacts">
      <li>
        <svg viewBox="0 0 24 24" aria-hidden="true"><path d="M6.6 10.8a15.1 15.1 0 0 0 6.6 6.6l2.2-2.2c.3-.3.7-.4 1-.2 1.1.4 2.3.6 3.6.6.6 0 1 .4 1 1V20c0 .6-.4 1-1 1A17 17 0 0 1 3 4c0-.6.4-1 1-1h3.5c.6 0 1 .4 1 1 0 1.3.2 2.5.6 3.6.1.3 0 .7-.2 1z"/></svg>
        +41 79555 0142
      </li>
      <li>
        <svg viewBox="0 0 24 24" aria-hidden="true"><path d="M2 5h20v14H2z M2 5l10 8 10-8" /></svg>
        mark@zub.capital
      </li>
      <li>
        <svg viewBox="0 0 24 24" aria-hidden="true"><circle cx="12" cy="12" r="10"/></svg>
        www.zub.capital
      </li>
    </ul>
  </section>

  <section class="card card--back" aria-label="Business card back">
    <div class="wordmark"><span class="wordmark__dot"></span>zub capital</div>
  </section>

</body>
</html>
```